Tour operator needs simple coded WordPress site (updated extra payment for coding and guaranteed)

[update 9/7/2015]
If you design a new logo and it gets accepted, even if we use another template with your logo you will get $50
[update 8/7/2015]
Update on questions about dual-language
For dual languages we are happy to set up a second site with the same designs in a second language.
For the design aspect just allow the user to switch between languages with an icon.
For the coding, a replica of the site on a second server will do (to save messing around with multiple language plugins) - we will populate it with Chinese text
[original post]
Simple coded WordPress site for tours
You can choose to design only or design and code ($340 design, $150 bonus for coding)
Open design brief - use your creativity
Will be in 2 languages (English and Chinese) but design needs only to be in one language
Winning design will be chosen only from home page, but the winner must make a second standard template page when chosen at no extra cost.
Must be responsive design
We only need homepage and standard template page design and coding, we will populate the pages
You can use design ideas from our pamphlet if you like - attached
Only a sample logo and colors on website and pamphlet - feel free to change as the current ones seem restrictive
Current website framework only to give an idea of the number of pages and basic menu structure (no need to use existing navigation style or any style at all for that matter, open brief)
http://brightwattlejourneys.com.au/
Target Market(s)
Chinese parents of kids 10-14 (the kids will take the tour)
Industry/Entity Type
Tour
Number of Pages Required
2 page
Look and feel
Each slider illustrates characteristics of the customer's brand and the style your logo design should communicate.

```html
<!DOCTYPE html>
<html lang="en">
<head>
<meta charset="utf-8">
<title>Bright Wattle Journeys</title>
<link href="https://fonts.googleapis.com/css2?family=Oxygen:wght@300;400;700&family=Roboto:wght@500;700&display=swap" rel="stylesheet">
<style>
:root{
  --navy:#2f3f7f;
  --navy-dark:#253468;
  --gold:#f3ad1c;
  --ink:#2b2b2b;
  --muted:#444;
  --white:#fff;
  --btn:#2e2e2e;
}
*{box-sizing:border-box;margin:0;padding:0}
html,body{width:1200px;height:1048px;overflow:hidden;background:var(--white)}
body{position:relative;font-family:'Oxygen',sans-serif;color:var(--ink)}
.site-header{position:absolute;top:0;left:0;width:1200px;height:95px}
.lang-switch{position:absolute;left:815px;top:22px;width:118px;height:31px;background:#2b2b2b;border:1px solid #111;border-radius:3px;color:#fff;font-size:13px;display:flex;align-items:center;gap:8px;padding-left:17px}
.lang-flag{width:21px;height:14px;background:linear-gradient(#c8102e,#c8102e) center/100% 3px no-repeat,linear-gradient(#c8102e,#c8102e) center/3px 100% no-repeat,#2a3f8f}
.book-now{position:absolute;left:950px;top:21px;width:89px;height:33px;background:var(--gold);color:#fff;font-size:14px;font-weight:700;display:flex;align-items:center;justify-content:center;border-radius:2px}
.main-nav{position:absolute;top:95px;left:0;width:1200px;height:42px;background:var(--navy);display:flex;padding-left:414px}
.main-nav a{height:42px;display:flex;align-items:center;justify-content:center;color:#fff;text-decoration:none;font-size:15px;border-right:1px solid #4a5a98}
.main-nav a:first-child{border-left:1px solid #4a5a98}
.main-nav a.active{box-shadow:inset 0 -3px 0 var(--gold)}
.brand{position:absolute;left:180px;top:12px;width:166px;height:166px;border-radius:50%;background:var(--white);border:5px solid var(--navy);z-index:3;display:flex;align-items:center;justify-content:center;text-align:center;color:var(--navy);font-family:'Roboto',sans-serif;font-weight:700;font-size:19px;line-height:1.15;box-shadow:0 2px 6px rgba(0,0,0,.25)}
.hero{position:absolute;top:137px;left:0;width:1200px;height:419px;background:linear-gradient(180deg,#c9a56a 0%,#e2a54a 35%,#a9682c 60%,#7a4f2d 100%)}
.hero-title{position:absolute;left:160px;top:286px;color:#fff;font-family:'Roboto',sans-serif;font-weight:700;font-size:26px;line-height:34px;text-shadow:1px 2px 3px rgba(0,0,0,.6)}
.hero-arrow{position:absolute;top:206px}
.hero-badge{position:absolute;left:944px;top:265px;width:95px;height:95px;border-radius:50%;border:2px solid rgba(255,255,255,.7)}
.features{position:absolute;top:524px;left:0;width:1200px}
.feature{position:absolute;width:260px;text-align:center}
.feature-icon{width:144px;height:144px;margin:0 auto;border-radius:50%;background:var(--white);display:flex;align-items:center;justify-content:center}
.feature-title{margin-top:2px;font-size:16px;font-weight:700;color:var(--ink)}
.feature.active .feature-title{color:var(--navy)}
.divider{position:absolute;top:719px;left:130px;width:940px;height:2px;background:linear-gradient(90deg,transparent,#bbb 20%,#bbb 80%,transparent)}
.about{position:absolute;top:766px;left:0;width:1200px;text-align:center}
.about h2{font-family:'Roboto',sans-serif;font-weight:500;font-size:28px;color:var(--navy)}
.about h2 .accent{color:var(--gold)}
.about-rule{position:relative;width:640px;height:20px;margin:4px auto 0}
.about-lead{margin-top:8px;font-size:13px;font-weight:700;line-height:19px;padding:0 175px}
.about-body{margin-top:10px;font-size:13px;font-weight:300;line-height:19px;color:var(--muted);padding:0 180px}
.read-more{display:inline-block;margin-top:16px;background:var(--btn);color:#fff;font-size:14px;font-weight:700;padding:7px 14px;border-radius:3px}
.site-footer{position:absolute;top:1006px;left:0;width:1200px;height:42px;background:var(--navy);color:#fff;font-size:12.5px}
.copyright{position:absolute;left:161px;top:14px}
.social{position:absolute;right:161px;top:2px;display:flex;gap:8px}
.social span{width:38px;height:38px;border-radius:50%;background:#dfe4f0;border:2px solid #fff}
</style>
</head>
<body>
<header class="site-header">
  <div class="brand">Bright Wattle<br>Journeys</div>
  <div class="lang-switch"><span class="lang-flag"></span>English
    <svg width="10" height="8" viewBox="0 0 10 8"><path d="M1 2l4 4 4-4" fill="none" stroke="#fff" stroke-width="1.6"/></svg></div>
  <div class="book-now">Book Now</div>
</header>
<nav class="main-nav">
  <a class="active" style="width:147px">HOME</a>
  <a style="width:152px">TOURS</a>
  <a style="width:173px">CONTACT</a>
  <a style="width:152px">ABOUT</a>
</nav>
<section class="hero" role="img" aria-label="Sunset photo of a harbour with the opera house and arch bridge reflected in the water">
  <svg class="hero-arrow" style="left:102px" width="20" height="30" viewBox="0 0 20 30"><path d="M16 2L4 15l12 13" fill="none" stroke="#fff" stroke-width="3"/></svg>
  <svg class="hero-arrow" style="left:1078px" width="20" height="30" viewBox="0 0 20 30"><path d="M4 2l12 13L4 28" fill="none" stroke="#fff" stroke-width="3"/></svg>
  <h1 class="hero-title">EDUCATIONAL, SAFE, CULTURALLY BRIGHT WATTLE<br>JOURNEYS ENLIGHTENING AND FUN.</h1>
  <div class="hero-badge"></div>
</section>
<section class="features">
  <div class="feature active" style="left:141px">
    <div class="feature-icon">
      <svg width="120" height="120" viewBox="0 0 120 120"><circle cx="60" cy="60" r="58" fill="none" stroke="var(--navy)" stroke-width="2"/><circle cx="60" cy="60" r="53" fill="var(--navy)"/><path d="M30 50l30-13 30 13-30 13z" fill="#fff"/><path d="M42 56v14c10 7 26 7 36 0V56l-18 8z" fill="#fff"/><rect x="34" y="76" width="46" height="10" rx="5" fill="#fff" transform="rotate(18 57 81)"/></svg>
    </div>
    <div class="feature-title">Educational And Cultural</div>
  </div>
  <div class="feature" style="left:467px">
    <div class="feature-icon">
      <svg width="120" height="120" viewBox="0 0 120 120"><circle cx="60" cy="60" r="58" fill="none" stroke="var(--gold)" stroke-width="2"/><circle cx="60" cy="60" r="53" fill="var(--gold)"/><path d="M60 30c10 6 18 7 26 7 0 26-8 40-26 50-18-10-26-24-26-50 8 0 16-1 26-7z" fill="#fff"/><path d="M46 58l10 10 18-20" fill="none" stroke="var(--gold)" stroke-width="7"/></svg>
    </div>
    <div class="feature-title">Safe And Secure</div>
  </div>
  <div class="feature" style="left:794px">
    <div class="feature-icon">
      <svg width="120" height="120" viewBox="0 0 120 120"><circle cx="60" cy="60" r="58" fill="none" stroke="var(--gold)" stroke-width="2"/><circle cx="60" cy="60" r="53" fill="var(--gold)"/><circle cx="66" cy="60" r="22" fill="none" stroke="#fff" stroke-width="4"/><path d="M44 60h44M66 38v44" stroke="#fff" stroke-width="3"/><path d="M28 50l40 8-2 6-40-8z" fill="#fff"/></svg>
    </div>
    <div class="feature-title">Travel insurance</div>
  </div>
</section>
<div class="divider"></div>
<section class="about">
  <h2><span class="accent">ABOUT</span> BRIGHT WATTLE JOURNEYS</h2>
  <svg class="about-rule" viewBox="0 0 640 20"><line x1="0" y1="10" x2="300" y2="10" stroke="#ccc" stroke-width="3"/><line x1="340" y1="10" x2="640" y2="10" stroke="#ccc" stroke-width="3"/><circle cx="320" cy="10" r="9" fill="var(--gold)"/><circle cx="320" cy="10" r="4" fill="var(--navy)"/></svg>
  <p class="about-lead">At Bright Wattle Journeys We Are Passionate About Educational Travel And Opportunities For Students To Gain Academic And Cultural Understanding Of Australia.</p>
  <p class="about-body">14 day premium cultural and educational tours to Australian cities. Educational, safe, culturally enlightening and fun. Learn about educational institutions, history, sports, laws and customs, food and culture while improving your English.</p>
  <span class="read-more">READ MORE</span>
</section>
<footer class="site-footer">
  <div class="copyright">© 2015 &nbsp;BRIGHT WATTLE JOURNEYS. All Rights Reserved.</div>
  <div class="social"><span aria-label="Social link"></span><span aria-label="Social link"></span><span aria-label="Social link"></span></div>
</footer>
</body>
</html>
```